New Business Card Design Project

We would like a business card that represents the sale of boat, home, auto, and life insurance.

The logo can change colors to meet the look of the design if needed.

Industry/Entity Type

Business

```html
<!DOCTYPE html>
<html lang="en">
<head>
<meta charset="UTF-8">
<title>Harborline Financial – Business Card</title>
<link rel="stylesheet" href="https://fonts.googleapis.com/css2?family=Open+Sans:wght@400;600;700&display=swap">
<style>
  :root {
    --stage: #d9d6d2;
    --card-black: #0b0b0d;
    --ink-white: #ffffff;
    --ink-soft: #e6e6e6;
    --accent-blue: #3a8fb0;
    --name-blue: #3f9ec4;
    --photo-top: #2a2420;
    --photo-bottom: #121214;
  }
  * { margin: 0; padding: 0; box-sizing: border-box; }
  html, body {
    width: 1200px;
    height: 768px;
    overflow: hidden;
    background: var(--stage);
    font-family: "Open Sans", Arial, sans-serif;
  }
  .canvas {
    position: relative;
    width: 1200px;
    height: 768px;
  }
  .card {
    position: absolute;
    top: 241px;
    width: 500px;
    height: 286px;
    background: var(--card-black);
    overflow: hidden;
    box-shadow: 0 8px 24px rgba(0,0,0,0.25);
  }
  .card-front { left: 80px; }
  .card-back { left: 620px; }

  /* Front */
  .brand {
    position: absolute;
    top: 50%;
    left: 50%;
    transform: translate(-50%, -50%);
    text-align: center;
    color: var(--ink-white);
  }
  .brand-row {
    display: flex;
    align-items: center;
    justify-content: center;
    gap: 12px;
  }
  .brand-dot {
    width: 18px;
    height: 18px;
    border-radius: 50%;
    background: var(--accent-blue);
  }
  .brand-name {
    font-size: 30px;
    font-weight: 600;
    letter-spacing: 2px;
    color: var(--ink-white);
  }
  .brand-tagline {
    margin-top: 8px;
    font-size: 17px;
    font-weight: 600;
    letter-spacing: 1.5px;
    color: var(--ink-white);
  }

  /* Back */
  .portrait {
    position: absolute;
    left: 20px;
    top: 40px;
    width: 230px;
    height: 246px;
    background: linear-gradient(180deg, var(--photo-top), var(--photo-bottom));
  }
  .card-bands {
    position: absolute;
    left: 0;
    top: 0;
  }
  .contact {
    position: absolute;
    left: 290px;
    top: 60px;
    color: var(--ink-soft);
  }
  .person-name {
    font-size: 15px;
    font-weight: 700;
    color: var(--name-blue);
  }
  .person-title {
    font-size: 9px;
    color: var(--ink-soft);
    margin-bottom: 12px;
  }
  .contact-list { list-style: none; }
  .contact-list li {
    display: flex;
    align-items: center;
    gap: 8px;
    font-size: 12px;
    line-height: 17px;
  }
  .contact-list svg { width: 10px; height: 10px; flex: none; }
  .address {
    margin-top: 8px;
    font-size: 12px;
    line-height: 16px;
    color: var(--ink-soft);
  }
</style>
</head>
<body>
<main class="canvas">

  <section class="card card-front" aria-label="Card front">
    <div class="brand">
      <div class="brand-row">
        <span class="brand-dot"></span>
        <span class="brand-name">HARBORLINE</span>
      </div>
      <div class="brand-tagline">investments &amp; insurance</div>
    </div>
  </section>

  <section class="card card-back" aria-label="Card back">
    <div class="portrait" role="img" aria-label="Portrait photo of the agent"></div>

    <svg class="card-bands" width="500" height="286" viewBox="0 0 500 286">
      <polygon points="0,218 0,232 250,262 250,250" fill="var(--accent-blue)"/>
      <polygon points="245,258 500,272 500,286 258,286" fill="var(--ink-white)"/>
    </svg>

    <div class="contact">
      <div class="person-name">Your Long Name</div>
      <div class="person-title">Your Title</div>
      <ul class="contact-list">
        <li>
          <svg viewBox="0 0 10 10"><path d="M2 1 L4 1 L4.5 3 L3.3 3.8 Q4.3 5.8 6.2 6.7 L7 5.5 L9 6 L9 8 Q5 9 1.5 4.5 Q1 2.5 2 1Z" fill="var(--accent-blue)"/></svg>
          000 0 0 000 00
        </li>
        <li>
          <svg viewBox="0 0 10 10"><rect x="2.5" y="0.5" width="5" height="9" rx="1" fill="var(--accent-blue)"/><rect x="3.5" y="1.8" width="3" height="5" fill="var(--card-black)"/></svg>
          (00) 0 0 0000 0000
        </li>
        <li>
          <svg viewBox="0 0 10 10"><rect x="0.5" y="2" width="9" height="6.5" fill="var(--accent-blue)"/><path d="M0.5 2 L5 5.8 L9.5 2" stroke="var(--card-black)" fill="none"/></svg>
          yourname@yourwebiste.com
        </li>
        <li>
          <svg viewBox="0 0 10 10"><circle cx="5" cy="5" r="4.3" fill="none" stroke="var(--accent-blue)" stroke-width="1.2"/><path d="M0.7 5 H9.3 M5 0.7 Q2.5 5 5 9.3 M5 0.7 Q7.5 5 5 9.3" stroke="var(--accent-blue)" fill="none"/></svg>
          www.yourwebsite.com
        </li>
      </ul>
      <p class="address">Your office or residentianal address<br>in just two line with pin code.</p>
    </div>
  </section>

</main>
</body>
</html>
```